Logo, Web and Mobile Designs for enterprise social media platform

All the details are in the attached document, please start reading the scope document first which explains what is this project about and the details about the needed deliverables, after that please read the UI_Requirements document which will detail what is expected regarding the coded web version since this is a coded contest, it is very important that you meet the UI requirements or suggest something else but we will need to agree first before working on the coded version

Good Luck

Target Market(s)

Enterprise Social Media

Industry/Entity Type

Media

Coding

Coded - Design and coding required

Number of Pages Required

5+ page

Font styles to use
Sans Serif

Requirements
Must have
• All the must haves are listed in the scope document so please check before you start

```html
<!DOCTYPE html>
<html lang="en">
<head>
<meta charset="utf-8">
<title>Teamora</title>
<link href="https://fonts.googleapis.com/css2?family=Cinzel:wght@400;700&family=Open+Sans:wght@400;600;700&display=swap" rel="stylesheet">
<style>
:root{
  --teal:#1a8496;
  --teal-dark:#0f6676;
  --gold:#b88c36;
  --gold-dark:#8d6620;
  --ink:#4a4a4a;
  --navy:#17324b;
  --navy-deep:#10243a;
  --panel:#f7f7f7;
  --line:#dcdcdc;
  --footer:#141414;
  --muted:#9a9a9a;
}
*{margin:0;padding:0;box-sizing:border-box}
html,body{width:1200px;height:878px;overflow:hidden;background:#fff;font-family:"Open Sans",sans-serif}
a{text-decoration:none}
.page{position:relative;width:1200px;height:878px}
.site-header{position:absolute;left:0;top:0;width:1200px;height:149px;border-top:3px solid var(--teal-dark);background:#fff}
.brand{position:absolute;left:98px;top:39px;display:flex;align-items:center;gap:14px}
.brand-dot{width:50px;height:50px;border-radius:50%;background:var(--teal)}
.brand-name{font-family:"Cinzel",serif;font-weight:400;font-size:30px;color:var(--ink);letter-spacing:1px}
.main-nav a{position:absolute;top:38px;font-size:12.5px;color:#555;text-transform:uppercase;display:flex;align-items:center;gap:7px}
.main-nav svg{width:11px;height:11px;fill:#777}
.search-btn{position:absolute;left:1065px;top:26px;width:35px;height:35px;border-radius:50%;background:var(--teal);display:flex;align-items:center;justify-content:center}
.btn{position:absolute;display:flex;align-items:center;justify-content:center;gap:10px;color:#fff;font-weight:700;font-size:12.5px;text-transform:uppercase;border-radius:2px;text-decoration:none}
.btn-login{left:869px;top:87px;width:101px;height:35px;background:linear-gradient(var(--teal),var(--teal-dark))}
.btn-register{left:998px;top:87px;width:102px;height:35px;background:linear-gradient(#c99b42,var(--gold-dark))}
.hero{position:absolute;left:0;top:149px;width:1200px;height:463px;background:linear-gradient(100deg,#2f6683 0%,#1f4866 40%,var(--navy) 65%,var(--navy-deep) 100%);overflow:hidden}
.hero-photo{position:absolute;left:0;top:0;width:840px;height:463px;background:linear-gradient(180deg,rgba(60,120,150,.35) 0%,rgba(40,80,110,.2) 70%,#e8eaec 88%,#f2f3f4 100%)}
.arrow{position:absolute;top:206px;width:14px;height:44px}
.hero-copy{position:absolute;right:100px;top:141px;text-align:right;color:#fff}
.hero-copy h1{font-family:"Cinzel",serif;font-weight:400;font-size:31px;letter-spacing:.5px;line-height:40px}
.hero-copy p{margin-top:8px;font-size:12.5px;line-height:26px;color:#e4ecf2}
.btn-more{left:955px;top:255px;width:145px;height:40px;background:linear-gradient(#a47c30,#7e5b1c);font-size:12px}
.comments{position:absolute;left:0;top:612px;width:1200px;height:209px;background:var(--panel)}
.comment-box{position:absolute;left:99px;top:31px;width:1001px;height:152px;border:1px solid var(--line);background:#fbfbfb}
.avatar{position:absolute;left:18px;top:20px;width:75px;height:72px;background:#d7e7f6}
.comment-input{position:absolute;left:120px;top:20px;width:855px;height:72px;border:1px solid var(--line);background:#fff;padding:13px 20px;font-size:12.5px;color:#a5a5a5;text-transform:uppercase}
.plugin-link{position:absolute;left:120px;top:107px;display:flex;align-items:center;gap:10px;font-size:13px;color:#666}
.plugin-link .label{text-decoration:underline}
.plugin-link .sq{width:14px;height:14px;background:var(--teal);display:block}
.btn-comment{left:860px;top:106px;width:116px;height:34px;background:linear-gradient(var(--teal),var(--teal-dark))}
.site-footer{position:absolute;left:0;top:821px;width:1200px;height:57px;background:var(--footer);font-size:9.5px;letter-spacing:1px;color:var(--muted);text-transform:uppercase}
.site-footer span{position:absolute;top:23px;white-space:nowrap}
.social{position:absolute;left:1017px;top:22px;display:flex;gap:14px}
.social i{width:12px;height:12px;border-radius:50%;background:#8a8a8a;display:block}
</style>
</head>
<body>
<div class="page">
  <header class="site-header">
    <div class="brand"><span class="brand-dot"></span><span class="brand-name">TEAMORA</span></div>
    <nav class="main-nav">
      <a href="#" style="left:502px"><svg viewBox="0 0 10 10"><path d="M5 1 0 5h1.5v4h2.5V6.5h2V9h2.5V5H10z"/></svg>Home</a>
      <a href="#" style="left:606px"><svg viewBox="0 0 10 10"><circle cx="5" cy="3" r="2.3"/><path d="M1 10c0-3 1.8-4.3 4-4.3S9 7 9 10z"/></svg>About</a>
      <a href="#" style="left:705px"><svg viewBox="0 0 10 10"><circle cx="5" cy="5" r="4"/><circle cx="5" cy="5" r="1.5" fill="#fff"/></svg>Events</a>
      <a href="#" style="left:811px"><svg viewBox="0 0 10 10"><rect x="0" y="1" width="10" height="8"/><rect x="1.5" y="2.5" width="3" height="2.5" fill="#fff"/></svg>News</a>
      <a href="#" style="left:915px"><svg viewBox="0 0 10 10"><path d="M2 0.5 4 3 3 4.2c.6 1.3 1.5 2.2 2.8 2.8L7 6l2.5 2L8.3 9.7C4.5 9.5.5 5.5.3 1.7z"/></svg>Contacts</a>
    </nav>
    <a class="search-btn" href="#" aria-label="Search"><svg width="13" height="13" viewBox="0 0 13 13"><circle cx="5.5" cy="5.5" r="3.8" fill="none" stroke="#fff" stroke-width="2"/><path d="M8.3 8.3 11.5 11.5" stroke="#fff" stroke-width="2.2"/></svg></a>
    <a class="btn btn-login" href="#"><svg width="10" height="11" viewBox="0 0 10 11"><rect x="1" y="5" width="8" height="6" fill="#fff"/><path d="M3 5V3.3a2 2 0 0 1 4 0V5" fill="none" stroke="#fff" stroke-width="1.5"/></svg>Login</a>
    <a class="btn btn-register" href="#"><svg width="11" height="11" viewBox="0 0 11 11"><path d="M0 11l.7-3L8 .7 10.3 3 3 10.3z" fill="#fff"/></svg>Register</a>
  </header>

  <section class="hero">
    <div class="hero-photo" role="img" aria-label="Photo of a smiling woman working on a laptop at a white desk with glowing network icons"></div>
    <svg class="arrow" style="left:34px" viewBox="0 0 14 44"><path d="M13 1 1 22l12 21" fill="none" stroke="#d8e4ec" stroke-width="1.2"/></svg>
    <svg class="arrow" style="left:1148px" viewBox="0 0 14 44"><path d="M1 1l12 21L1 43" fill="none" stroke="#d8e4ec" stroke-width="1.2"/></svg>
    <div class="hero-copy">
      <h1>WELCOME TO TEAMORA</h1>
      <p>Sed ut perspiciatis unde omnis iste natus error sit voluptats et<br>rchitecto beatae vitae cta sunt expliodit aut fugit,&nbsp; sed quia</p>
    </div>
    <a class="btn btn-more" href="#">View more &gt;&gt;</a>
  </section>

  <section class="comments">
    <div class="comment-box">
      <div class="avatar" role="img" aria-label="Default user avatar"></div>
      <div class="comment-input">Add a comments &nbsp;...</div>
      <a class="plugin-link" href="#"><span class="sq"></span><span class="label">Network social plugin</span></a>
      <a class="btn btn-comment" href="#">Comment</a>
    </div>
  </section>

  <footer class="site-footer">
    <span style="left:100px">© 2015. Teamora. All rights reserved.</span>
    <span style="left:442px">Phone : + 321 5550 104</span>
    <span style="left:598px">Email :&nbsp; teamora.com</span>
    <span style="left:931px">Follow us :</span>
    <div class="social"><i></i><i></i><i></i><i></i></div>
  </footer>
</div>
</body>
</html>
```